Linking together of the glow Wheel, rise and roam and brightfold.

Lift the fog (the glow wheel), rise and roam, and Brightfold are 3 treatment programs for people with chronic pain.
Lift the fog is 1st. Here I aim to half peoples pain, then halve it again and again until it is gone, or they no longer care about it.
Rise and roam is a rehabilitation program. We get people to identify the things that their pain has taken from them, and then we take it back. (ie Take back what's yours')
Brightfold is a disease prevention program. It is targeted at identifying diseases of ageing and slowing their progression, or hopefully preventing their onset.
My wife has suggested we linked them together like cogs working together. As one cog turns all the others do, thus as we decrease pain, we start the wheels turning of taking back what you have lost.
I have attach some cogs pictures so you can see what I mean.
I was thinking that the glow wheel could be like spokes on a bicycle wheel.
For Rise and roam similar to the glow wheel can you have 5 sections
1. Mindset
2. Workout
3. Diet
5. Recover
6. Socialise
For Brightfold, I am still developing its components. I will leave that to you.
Send me some questions if this doesn't make sense.
When I set this project up, I had set it up for a designer I have been working with. He completed 2 other jobs for me and hasn't got to this. Can it please be extended? Cheers Tom

```html
<!DOCTYPE html>
<html lang="en">
<head>
<meta charset="utf-8">
<title>Lift the fog · Rise and roam · Brightfold</title>
<link href="https://fonts.googleapis.com/css2?family=Oswald:wght@400;500;600&display=swap" rel="stylesheet">
<style>
  :root{
    --royal:#1456a6;
    --cog-blue:#1a78bc;
    --cog-deep:#1565b0;
    --navy:#16305e;
    --teal-navy:#1b5078;
    --slate:#245aa0;
    --white:#ffffff;
    --ink:#1d2433;
    --sky:#5bc4ef;
    --mist:#a9c8ea;
    --periwinkle:#8fa9dc;
    --steel:#2a4e8f;
    --petrol:#1c4b6e;
    --midnight:#1b2f55;
    --abyss:#16284a;
    --fern:#9fd08c;
    --sage:#c4e0b4;
    --butter:#f5e59a;
    --sun:#f7d860;
    --gold:#ecc535;
  }
  html,body{margin:0;padding:0;width:1199px;height:1200px;overflow:hidden;background:var(--white);}
  .canvas{display:block;width:1199px;height:1200px;}
  .label{font-family:"Oswald",sans-serif;font-weight:500;text-transform:uppercase;}
  .label--dark{fill:var(--ink);}
  .label--light{fill:var(--white);}
  .wordmark{font-family:"Oswald",sans-serif;font-weight:600;fill:var(--white);text-transform:uppercase;letter-spacing:1px;}
  .band{fill:var(--royal);}
  .flow-arrow{fill:none;stroke:var(--royal);stroke-width:7;}
  .arrow-head{fill:var(--royal);}
</style>
</head>
<body>
<svg class="canvas" viewBox="0 0 1920 1920" preserveAspectRatio="none" xmlns="http://www.w3.org/2000/svg">

  <!-- connecting bands -->
  <g class="bands">
    <path class="band" d="M400,790 C600,790 700,650 750,520 L990,680 C780,690 640,820 636,1030 Z"/>
    <path class="band" d="M370,1350 C560,1350 690,1220 730,1060 L940,1235 C760,1240 600,1380 600,1580 Z"/>
    <path class="band" d="M908,1320 C1100,1320 1230,1180 1270,1040 L1470,1210 C1300,1225 1140,1380 1137,1550 Z"/>
    <circle class="band" cx="408" cy="1017" r="228"/>
    <circle class="band" cx="370" cy="1575" r="228"/>
    <circle class="band" cx="908" cy="1545" r="228"/>
  </g>

  <!-- programme names -->
  <text class="wordmark" x="408" y="1040" font-size="64" text-anchor="middle">Lift the fog</text>
  <text class="wordmark" x="370" y="1600" font-size="62" text-anchor="middle">Rise and roam</text>
  <text class="wordmark" x="908" y="1572" font-size="70" text-anchor="middle">Brightfold</text>

  <!-- rotation arrows -->
  <path class="flow-arrow" d="M692,492 A290,290 0 0 1 1080,178"/>
  <polygon class="arrow-head" points="1108,190 1062,156 1070,196"/>
  <path class="flow-arrow" d="M895,1276 A270,270 0 0 0 1195,880"/>
  <polygon class="arrow-head" points="1195,852 1176,898 1220,882"/>
  <path class="flow-arrow" d="M1338,725 A300,300 0 0 1 1768,975"/>
  <polygon class="arrow-head" points="1768,1006 1746,964 1790,966"/>

  <!-- glow wheel cog -->
  <g class="glow-wheel" transform="translate(982,447)">
    <g class="cog-teeth" fill="var(--cog-deep)">
      <rect x="-25" y="-252" width="50" height="70" rx="6" transform="rotate(0)"/>
      <rect x="-25" y="-252" width="50" height="70" rx="6" transform="rotate(30)"/>
      <rect x="-25" y="-252" width="50" height="70" rx="6" transform="rotate(60)"/>
      <rect x="-25" y="-252" width="50" height="70" rx="6" transform="rotate(90)"/>
      <rect x="-25" y="-252" width="50" height="70" rx="6" transform="rotate(120)"/>
      <rect x="-25" y="-252" width="50" height="70" rx="6" transform="rotate(150)"/>
      <rect x="-25" y="-252" width="50" height="70" rx="6" transform="rotate(180)"/>
      <rect x="-25" y="-252" width="50" height="70" rx="6" transform="rotate(210)"/>
      <rect x="-25" y="-252" width="50" height="70" rx="6" transform="rotate(240)"/>
      <rect x="-25" y="-252" width="50" height="70" rx="6" transform="rotate(270)"/>
      <rect x="-25" y="-252" width="50" height="70" rx="6" transform="rotate(300)"/>
      <rect x="-25" y="-252" width="50" height="70" rx="6" transform="rotate(330)"/>
    </g>
    <circle r="215" fill="var(--cog-deep)"/>
    <circle r="200" fill="none" stroke="#9fb6cf" stroke-width="5"/>
    <g class="wheel-segments" fill="none" stroke-width="190">
      <circle r="95" stroke="var(--sky)" stroke-dasharray="45.92 600" transform="rotate(-90)"/>
      <circle r="95" stroke="var(--mist)" stroke-dasharray="45.92 600" transform="rotate(-62.31)"/>
      <circle r="95" stroke="var(--periwinkle)" stroke-dasharray="45.92 600" transform="rotate(-34.62)"/>
      <circle r="95" stroke="var(--cog-blue)" stroke-dasharray="45.92 600" transform="rotate(-6.92)"/>
      <circle r="95" stroke="var(--steel)" stroke-dasharray="45.92 600" transform="rotate(20.77)"/>
      <circle r="95" stroke="var(--petrol)" stroke-dasharray="45.92 600" transform="rotate(48.46)"/>
      <circle r="95" stroke="var(--midnight)" stroke-dasharray="45.92 600" transform="rotate(76.15)"/>
      <circle r="95" stroke="var(--abyss)" stroke-dasharray="45.92 600" transform="rotate(103.85)"/>
      <circle r="95" stroke="var(--fern)" stroke-dasharray="45.92 600" transform="rotate(131.54)"/>
      <circle r="95" stroke="var(--sage)" stroke-dasharray="45.92 600" transform="rotate(159.23)"/>
      <circle r="95" stroke="var(--butter)" stroke-dasharray="45.92 600" transform="rotate(186.92)"/>
      <circle r="95" stroke="var(--sun)" stroke-dasharray="45.92 600" transform="rotate(214.62)"/>
      <circle r="95" stroke="var(--gold)" stroke-dasharray="45.92 600" transform="rotate(242.31)"/>
    </g>
    <circle r="95" fill="#ffffff" fill-opacity="0.14"/>
    <g class="wheel-labels" font-size="12" text-anchor="middle">
      <text class="label label--dark" x="134" transform="rotate(-76.15)" dy="4">Somatic/visceral</text>
      <text class="label label--dark" x="134" transform="rotate(-48.46)" dy="4">Cause</text>
      <text class="label label--dark" x="134" transform="rotate(-20.77)" dy="4">Contributing</text>
      <text class="label label--light" x="134" transform="rotate(6.92)" dy="4">Myofascial</text>
      <text class="label label--light" x="134" transform="rotate(34.6)" dy="4">Bony</text>
      <text class="label label--light" x="134" transform="rotate(62.3)" dy="4">Inflammatory</text>
      <text class="label label--light" x="134" transform="rotate(90)" dy="4">Mechanical</text>
      <text class="label label--light" x="-134" transform="rotate(-62.3)" dy="4">Vascular</text>
      <text class="label label--dark" x="-134" transform="rotate(-34.6)" dy="4">Neuropathic</text>
      <text class="label label--dark" x="-134" transform="rotate(-6.9)" dy="4">Sensitisation</text>
      <text class="label label--dark" transform="rotate(20.8)"><tspan x="-134" dy="-3">Emotional and</tspan><tspan x="-134" dy="13">cognitive</tspan></text>
      <text class="label label--dark" x="-134" transform="rotate(48.5)" dy="4">Social</text>
      <text class="label label--dark" x="-134" transform="rotate(76.2)" dy="4">Sleep</text>
    </g>
    <circle r="66" fill="var(--royal)"/>
    <text class="wordmark" font-size="22" text-anchor="middle"><tspan x="0" y="-3">Lift the</tspan><tspan x="0" y="22">fog</tspan></text>
  </g>

  <!-- rise and roam cog -->
  <g class="rise-roam-wheel" transform="translate(943,1010)">
    <circle r="238" fill="none" stroke="var(--royal)" stroke-width="12" stroke-dasharray="55 30"/>
    <g class="cog-teeth" fill="var(--white)">
      <rect x="-28" y="-258" width="56" height="70" rx="8" transform="rotate(180)"/>
      <rect x="-28" y="-258" width="56" height="70" rx="8" transform="rotate(210)"/>
      <rect x="-28" y="-258" width="56" height="70" rx="8" transform="rotate(240)"/>
      <rect x="-28" y="-258" width="56" height="70" rx="8" transform="rotate(265)"/>
      <rect x="-28" y="-258" width="56" height="70" rx="8" transform="rotate(100)"/>
    </g>
    <circle r="215" fill="var(--white)"/>
    <g class="wheel-segments" fill="none" stroke-width="185">
      <circle r="92.5" stroke="var(--cog-blue)" stroke-dasharray="116.2 600" transform="rotate(-90)"/>
      <circle r="92.5" stroke="var(--navy)" stroke-dasharray="116.2 600" transform="rotate(-18)"/>
      <circle r="92.5" stroke="#163361" stroke-dasharray="116.2 600" transform="rotate(54)"/>
      <circle r="92.5" stroke="var(--teal-navy)" stroke-dasharray="116.2 600" transform="rotate(126)"/>
      <circle r="92.5" stroke="var(--slate)" stroke-dasharray="116.2 600" transform="rotate(198)"/>
    </g>
    <g class="spokes" stroke="var(--white)" stroke-width="16">
      <line x1="0" y1="0" x2="190" y2="0" transform="rotate(-90)"/>
      <line x1="0" y1="0" x2="190" y2="0" transform="rotate(-18)"/>
      <line x1="0" y1="0" x2="190" y2="0" transform="rotate(54)"/>
      <line x1="0" y1="0" x2="190" y2="0" transform="rotate(126)"/>
      <line x1="0" y1="0" x2="190" y2="0" transform="rotate(198)"/>
    </g>
    <g class="wheel-labels" font-size="22" text-anchor="middle">
      <text class="label label--light" x="138" transform="rotate(-54)" dy="8">Mindset</text>
      <text class="label label--light" x="138" transform="rotate(18)" dy="8">Workout</text>
      <text class="label label--light" x="138" transform="rotate(90)" dy="8">Eat</text>
      <text class="label label--light" x="-138" transform="rotate(-18)" dy="8">Recover</text>
      <text class="label label--light" x="-138" transform="rotate(54)" dy="8">Socialise</text>
    </g>
    <circle r="84" fill="var(--white)"/>
    <circle r="70" fill="var(--royal)"/>
    <text class="wordmark" font-size="24" text-anchor="middle"><tspan x="0" y="-4">Rise and</tspan><tspan x="0" y="24">roam</tspan></text>
  </g>

  <!-- brightfold cog -->
  <g class="brightfold-wheel" transform="translate(1483,980)">
    <circle r="225" fill="none" stroke="var(--cog-deep)" stroke-width="22" stroke-dasharray="7 14"/>
    <circle r="222" fill="var(--cog-blue)"/>
    <circle r="103" fill="none" stroke="var(--white)" stroke-width="38"/>
    <g class="cross" stroke="var(--white)" stroke-width="14">
      <rect x="-38" y="-160" width="76" height="320" fill="var(--cog-blue)" stroke="none"/>
      <rect x="-160" y="-38" width="320" height="76" fill="var(--cog-blue)" stroke="none"/>
      <line x1="0" y1="-222" x2="0" y2="222"/>
      <line x1="-222" y1="0" x2="222" y2="0"/>
    </g>
    <g class="wheel-labels" font-size="22">
      <text class="label label--light" x="-125" y="-125" text-anchor="middle" transform="rotate(45,-125,-125)" dy="8">Recover</text>
      <text class="label label--light" x="125" y="-125" text-anchor="middle" transform="rotate(-45,125,-125)" dy="8">Evolve</text>
      <text class="label label--light" x="125" y="125" text-anchor="middle" transform="rotate(45,125,125)" dy="8">Workout</text>
      <text class="label label--light" x="-125" y="125" text-anchor="middle" transform="rotate(-45,-125,125)" dy="8">Eat</text>
    </g>
    <circle r="82" fill="var(--royal)"/>
    <text class="wordmark" y="9" font-size="26" text-anchor="middle">Brightfold</text>
  </g>

</svg>
</body>
</html>
```